Design a Website in Wordpress for an Australian Health Training Company in Health related courses

We require a WORDPRESS based Website (due to add on's we need to use for third party software) to replace our old site.
We offer national face to face delivery in medical reception, terminology and also administration.
The website will have around 6 pages and the ability to describe our main 6 courses (perhaps on the Courses page this may be tabs opening up to details for example?)
I have attached a previous sample of a Joomla site which was being developed (please do not feel you have to copy this - but I am just giving it as a sample - copying would be boring). But it gives an idea of look/feel and colours which may be suitable. Open to other ideas though.
I will provide some of the content, but would like the ability to finish the content myself.
Images and graphics are important. While a few medical photos re great - don't be tempted to us all pictures of doctors and nurses (although a couple would be good) - these are administrative courses so general corporate, eye catching visionary pictures of people in general are great. A medical type picture is also fine.
THE BOOKING system - will be via an ADD ON which will occur at the end of the project and is supplied by a third party software company (our student management system). This project will include up to 2 hours working with the Tech guys from the third party software to enable the ADD ON. If this ADD ON requires more time, we will pay hourly (although I do not expect it will).
Target Market(s)
Mostly a female market, many mature aged women target 25-45 yrs. Mixture of medical/health and corporate. Maybe a bit of mums returning to work and corporate inspiration.
Industry/Entity Type
It Company
Coding
Coded - Design and coding required
Number of Pages Required
5+ page
Requirements
Must have
- Wordpress
- Great graphics
- Interesting
- professional and clean
- Enquiry section (info Pak)
- Should have a University feel to it - Education
- Pages
- Home Page - About Us - Recruitment -Courses - Class Schedule - Traineeships Queensland Funding - Latest News Blog - Corporate Training- Contact us

```html
<!DOCTYPE html>
<html lang="en">
<head>
<meta charset="utf-8">
<title>Harbourne Institute of Training</title>
<link rel="stylesheet" href="https://fonts.googleapis.com/css2?family=Lora:wght@400;700&family=Roboto:wght@400;500;700&display=swap">
<style>
:root{
  --navy:#24385e;
  --navy-deep:#1d2f50;
  --orange:#f7923a;
  --ink:#2b2b2b;
  --text:#4a4a4a;
  --grey:#8a8a8a;
  --light:#efefef;
  --footer:#2b2b2b;
  --white:#fff;
  --serif:'Lora', Georgia, serif;
  --sans:'Roboto', Arial, sans-serif;
}
*{box-sizing:border-box;margin:0;padding:0}
html,body{width:1200px;height:2941px;overflow:hidden}
body{font-family:var(--sans);color:var(--text);background:var(--white);position:relative}
.abs{position:absolute}
.btn{display:inline-flex;align-items:center;justify-content:center;background:var(--orange);color:var(--white);font-weight:700;text-transform:uppercase;font-family:var(--sans)}
.brand{font-family:var(--serif);color:var(--navy);font-weight:700;text-transform:uppercase;text-align:center;line-height:1.15}

/* header */
.topline{left:0;top:0;width:1200px;height:6px;background:var(--navy)}
.header{left:0;top:6px;width:1200px;height:146px;background:var(--white)}
.header .brand{left:110px;top:30px;width:170px;font-size:17px}
.header .brand-mark{display:block;width:46px;height:46px;margin:10px auto 0;background:var(--navy)}
.search{left:622px;top:20px;width:154px;height:42px;border:1px solid #ccc;display:flex;align-items:center;padding-left:12px;font-size:11px;color:#999;letter-spacing:1px;gap:8px}
.btn-info{left:790px;top:20px;width:134px;height:42px;font-size:14px;gap:6px;border-radius:2px}
.btn-enrol{left:934px;top:20px;width:134px;height:42px;font-size:13px;background:var(--navy);gap:6px;border-radius:2px}
.nav{left:330px;top:88px;display:flex;align-items:center;height:38px}
.nav a{font-size:12px;color:var(--ink);text-decoration:none;padding:0 10px;line-height:1.25;border-right:1px solid #ccc;height:38px;display:flex;align-items:center}
.nav a:last-child{border-right:none}
.nav a.active{background:var(--navy);color:var(--white);padding:0 16px}

/* hero */
.hero{left:0;top:152px;width:1200px;height:450px;background:linear-gradient(110deg,#6e6e6e 0%,#9a9a9a 45%,#7b7b7b 100%)}
.hero h1{position:absolute;left:130px;top:290px;font-family:var(--sans);font-weight:700;font-size:48px;color:var(--white);letter-spacing:1px}
.hero .btn{position:absolute;left:132px;top:362px;width:152px;height:38px;font-size:15px;gap:6px}
.hero-arrow{width:50px;height:50px;border-radius:50%;background:var(--navy);display:flex;align-items:center;justify-content:center}

/* courses */
.courses{left:0;top:602px;width:1200px;height:266px;background:var(--navy)}
.section-title{font-family:var(--serif);font-weight:700;color:var(--orange);font-size:17px;text-transform:uppercase}
.courses .section-title{position:absolute;top:36px;width:100%;text-align:center}
.course-list{position:absolute;left:116px;top:98px;display:flex}
.course{width:160px;text-align:center;border-right:1px solid rgba(255,255,255,.15);height:130px}
.course:last-child{border-right:none}
.course .icon{width:66px;height:66px;border-radius:50%;background:var(--orange);margin:0 auto 14px;display:flex;align-items:center;justify-content:center}
.course p{color:var(--white);font-size:13px;font-weight:500;line-height:1.4}

/* welcome */
.welcome{left:0;top:868px;width:1200px;height:375px}
.welcome .eyebrow{position:absolute;left:132px;top:30px;font-size:14px;font-weight:700;color:var(--navy)}
.welcome .brand{position:absolute;left:132px;top:52px;font-size:25px;text-align:left;font-weight:400;border-bottom:1px solid var(--navy);padding-bottom:4px}
.welcome .copy{position:absolute;left:132px;top:118px;width:560px;font-size:11.5px;line-height:1.75}
.welcome .copy p{margin-bottom:12px}
.welcome .btn{position:absolute;left:132px;top:306px;width:120px;height:36px;font-size:11px;gap:5px}
.logo-panel{position:absolute;left:736px;top:72px;width:336px;height:260px;border-left:1px solid #e0e0e0;display:flex;flex-direction:column;align-items:center;justify-content:center;gap:16px}
.logo-panel .mark{width:110px;height:110px;background:var(--navy)}
.logo-panel .brand{position:static;font-size:18px;border:none;text-align:center}

/* info pack + why */
.infopack{left:0;top:1243px;width:600px;height:577px;background:#8a8a8a}
.infopack .title{position:absolute;left:132px;top:42px;font-family:var(--serif);font-weight:700;color:var(--white);font-size:17px}
.field{position:absolute;left:134px;width:386px;height:46px;background:var(--white);display:flex;align-items:center;padding-left:16px;gap:10px;font-size:12px;color:#333}
.field .chev{margin-left:auto;margin-right:16px}
.send{position:absolute;left:134px;top:404px;width:386px;height:58px;font-size:22px;letter-spacing:2px}
.why{left:600px;top:1243px;width:600px;height:577px;background:var(--navy)}
.why .section-title{position:absolute;left:46px;top:42px}
.why-list{position:absolute;left:48px;top:84px;width:460px}
.why-item{display:flex;gap:20px;height:96px}
.why-item .icon{flex:none;width:52px;height:52px;border-radius:50%;background:var(--orange);display:flex;align-items:center;justify-content:center}
.why-item h4{color:var(--white);font-size:12px;font-weight:700;margin:4px 0 6px}
.why-item p{color:#dfe4ee;font-size:10.5px;line-height:1.6}

/* blog */
.blog{left:0;top:1820px;width:1200px;height:468px;background:var(--light)}
.blog .section-title{position:absolute;left:132px;top:40px}
.blog-nav{position:absolute;left:1030px;top:38px;display:flex;gap:12px}
.card{position:absolute;top:115px;width:222px;height:307px;background:var(--white)}
.card .date{position:absolute;left:86px;top:-22px;width:50px;height:50px;border-radius:50%;background:var(--white);text-align:center;font-family:var(--serif);color:var(--orange);font-size:18px;line-height:1;padding-top:9px}
.card .date small{display:block;font-family:var(--sans);font-size:8px;color:#333;margin-top:3px}
.card .thumb{position:absolute;left:8px;top:14px;width:206px;height:150px}
.card h5{position:absolute;left:16px;top:180px;width:190px;font-size:12px;color:var(--ink);font-weight:700;line-height:1.35}
.card p{position:absolute;left:16px;top:216px;width:190px;font-size:10.5px;line-height:1.6;text-align:justify}
.card .more{position:absolute;left:16px;top:276px;font-size:10px;font-weight:700;color:var(--orange)}

/* testimonials */
.testimonials{left:0;top:2288px;width:1200px;height:334px;background:linear-gradient(90deg,#2c4068,#364c76 50%,#2c4068)}
.testimonials .title{position:absolute;top:42px;width:100%;text-align:center;font-family:var(--serif);color:var(--white);font-weight:700;font-size:17px}
.testimonials .rule{position:absolute;left:576px;top:70px;width:48px;height:3px;background:var(--orange)}
.quote{position:absolute;left:230px;top:122px;width:740px;color:var(--white);text-align:center;font-size:12.5px;line-height:1.7}
.author{position:absolute;left:512px;top:240px;display:flex;align-items:center;gap:14px}
.author .avatar{width:48px;height:48px;border-radius:50%;background:#c9b7a6;border:2px solid var(--white)}
.author b{display:block;color:var(--white);font-size:12px}
.author span{color:#cfd6e4;font-size:10px}

/* footer */
.footer{left:0;top:2622px;width:1200px;height:274px;background:var(--footer)}
.footer .brand{position:absolute;left:130px;top:40px;width:170px;color:var(--white);font-size:16px;font-weight:400}
.footer .brand-mark{display:block;width:70px;height:70px;margin:14px auto 0;background:var(--white)}
.vline{position:absolute;left:338px;top:36px;width:1px;height:190px;background:#555}
.foot-h{font-size:12px;font-weight:700;color:var(--white)}
.contact{position:absolute;left:362px;top:38px;width:230px}
.contact .region{margin-top:22px;font-size:10.5px;font-weight:700;color:var(--white)}
.contact .phone{font-size:10px;color:#ccc;margin-top:4px}
.enquiry{position:absolute;left:634px;top:38px}
.efield{position:absolute;width:222px;height:36px;background:var(--navy);color:var(--white);font-size:10px;padding:10px 12px}
.bottom{left:0;top:2896px;width:1200px;height:45px;background:var(--orange);display:flex;align-items:center;padding:0 136px;font-size:10px;color:var(--ink)}
.social{display:flex;gap:8px;margin-left:10px}
.social i{width:22px;height:22px;border-radius:50%;background:var(--navy);display:block}
</style>
</head>
<body>

<div class="abs topline"></div>

<header class="abs header">
  <div class="abs brand">Harbourne Institute of Training<span class="brand-mark"></span></div>
  <div class="abs search">
    <svg width="11" height="11" viewBox="0 0 12 12"><circle cx="5" cy="5" r="3.8" fill="none" stroke="#999" stroke-width="1.5"/><path d="M8 8l3 3" stroke="#999" stroke-width="1.5"/></svg>SEARCH
  </div>
  <a class="abs btn btn-info">
    <svg width="14" height="14" viewBox="0 0 14 14"><circle cx="7" cy="7" r="6.5" fill="#fff"/><rect x="6" y="6" width="2" height="5" fill="#f7923a"/><circle cx="7" cy="4" r="1.1" fill="#f7923a"/></svg>Info Pack
  </a>
  <a class="abs btn btn-enrol">
    <svg width="14" height="14" viewBox="0 0 14 14"><path d="M3 13V7l4-5 4 5v6z" fill="#fff"/></svg>Enrol Now
  </a>
  <nav class="abs nav">
    <a class="active">Home</a><a>About Us</a><a>Recruitment</a><a>Courses</a><a>Class<br>Schedule</a><a>Traineeships<br>Queensland Funding</a><a>Latest<br>News Blog</a><a>Corporate<br>Training</a><a>Contact<br>us</a>
  </nav>
</header>

<section class="abs hero" role="img" aria-label="Hand holding a magnifying glass over a grid of people icons">
  <div class="abs hero-arrow" style="left:36px;top:202px"><svg width="14" height="14" viewBox="0 0 14 14"><path d="M9 2L4 7l5 5" fill="none" stroke="#fff" stroke-width="2"/></svg></div>
  <div class="abs hero-arrow" style="left:1100px;top:202px"><svg width="14" height="14" viewBox="0 0 14 14"><path d="M5 2l5 5-5 5" fill="none" stroke="#fff" stroke-width="2"/></svg></div>
  <h1>RECRUITMENT</h1>
  <a class="btn">Read More <svg width="12" height="10" viewBox="0 0 12 10"><path d="M1 1l4 4-4 4M6 1l4 4-4 4" fill="none" stroke="#fff" stroke-width="1.6"/></svg></a>
</section>

<section class="abs courses">
  <h2 class="section-title">Our Courses</h2>
  <div class="course-list">
    <div class="course"><div class="icon"><svg width="30" height="30" viewBox="0 0 30 30"><rect x="4" y="9" width="22" height="16" rx="2" fill="#fff"/><rect x="11" y="5" width="8" height="5" fill="none" stroke="#fff" stroke-width="2"/><path d="M15 13v8M11 17h8" stroke="#f7923a" stroke-width="2.5"/></svg></div><p>Medical Reception &amp;<br>Terminology</p></div>
    <div class="course"><div class="icon"><svg width="30" height="30" viewBox="0 0 30 30"><circle cx="15" cy="10" r="5" fill="#fff"/><path d="M5 27c0-7 4-10 10-10s10 3 10 10z" fill="#fff"/></svg></div><p>Cert III Business<br>Administration (Medical)</p></div>
    <div class="course"><div class="icon"><svg width="30" height="30" viewBox="0 0 30 30"><path d="M15 26S3 18 3 10a6 6 0 0 1 12-2 6 6 0 0 1 12 2c0 8-12 16-12 16z" fill="#fff"/><path d="M5 15h6l2-4 3 7 2-3h7" fill="none" stroke="#f7923a" stroke-width="1.8"/></svg></div><p>Medical<br>Terminology</p></div>
    <div class="course"><div class="icon"><svg width="32" height="30" viewBox="0 0 32 30"><rect x="3" y="9" width="26" height="14" rx="2" fill="none" stroke="#fff" stroke-width="2"/><path d="M7 13h2M11 13h2M15 13h2M19 13h2M23 13h2M9 19h14" stroke="#fff" stroke-width="2"/></svg></div><p>Keyboard<br>and Typing</p></div>
    <div class="course"><div class="icon"><svg width="30" height="30" viewBox="0 0 30 30"><circle cx="15" cy="15" r="11" fill="#fff"/><path d="M9 9c3 1 4 4 2 6s1 5 3 6M19 6c-1 3 2 4 4 5M21 20c-2-1-4 0-4 3" fill="none" stroke="#f7923a" stroke-width="2"/></svg></div><p>Harbourne<br>Online</p></div>
    <div class="course"><div class="icon"><svg width="30" height="30" viewBox="0 0 30 30"><rect x="6" y="13" width="18" height="13" rx="2" fill="#fff"/><path d="M10 13V9a5 5 0 0 1 10 0v4" fill="none" stroke="#fff" stroke-width="2.5"/></svg></div><p>Confidentiality</p></div>
  </div>
</section>

<section class="abs welcome">
  <div class="eyebrow">WELCOME TO</div>
  <div class="brand">Harbourne Institute<br>of Training</div>
  <div class="copy">
    <p>Harbourne is Australia's Leading Provider of Educational, Training and Support Services for the Medical and Dental industry - enabling students to be immediately skilled and 'Job Ready' for a career in Health.</p>
    <p>Harbourne is a Registered Training Organisation offering specialised Medical Administration Training in over 15 locations Australia wide. Harbourne have trained thousands of students the required knowledge and skills to become successful health care administrators.</p>
    <p>Our unique Short Medical Reception and Terminology Course and our Full Qualification is Nationally Accredited and the go-to recognised qualification in industry.</p>
  </div>
  <a class="btn">Read More <svg width="11" height="9" viewBox="0 0 12 10"><path d="M1 1l4 4-4 4M6 1l4 4-4 4" fill="none" stroke="#fff" stroke-width="1.6"/></svg></a>
  <div class="logo-panel">
    <div class="mark"></div>
    <div class="brand">Harbourne Institute of Training</div>
  </div>
</section>

<section class="abs infopack">
  <h3 class="title">EMAIL ME AN INFO PACK</h3>
  <div class="field" style="top:86px"><svg width="11" height="11" viewBox="0 0 12 12"><circle cx="6" cy="3.5" r="3" fill="#333"/><path d="M0 12c0-4 3-5 6-5s6 1 6 5z" fill="#333"/></svg>Name</div>
  <div class="field" style="top:150px"><svg width="12" height="10" viewBox="0 0 12 10"><rect x=".5" y=".5" width="11" height="9" fill="none" stroke="#333"/><path d="M.5 .5l5.5 5 5.5-5" fill="none" stroke="#333"/></svg>E mail</div>
  <div class="field" style="top:214px"><svg width="12" height="12" viewBox="0 0 12 12"><rect x=".5" y="2" width="9" height="9.5" fill="none" stroke="#333"/><path d="M5 7l6-6" stroke="#333" stroke-width="1.5"/></svg>Course<svg class="chev" width="12" height="8" viewBox="0 0 12 8"><path d="M1 1l5 5 5-5" fill="none" stroke="#333" stroke-width="1.6"/></svg></div>
  <div class="field" style="top:278px"><svg width="12" height="12" viewBox="0 0 12 12"><circle cx="6" cy="6" r="5.5" fill="#333"/></svg>State</div>
  <div class="field" style="top:342px"><svg width="12" height="12" viewBox="0 0 12 12"><path d="M2 1l3 1-1 3 3 3 3-1 1 3-2 1C5 11 1 7 1 3z" fill="#333"/></svg>Mobile</div>
  <a class="btn send">SEND</a>
</section>

<section class="abs why">
  <h3 class="section-title">Why Harbourne Institute ?</h3>
  <div class="why-list">
    <div class="why-item"><div class="icon"><svg width="24" height="24" viewBox="0 0 24 24"><path d="M3 11h4v10H3zM8 11l4-8c2 0 3 1 2 4l-1 3h6c1 0 2 1 2 2l-2 7c0 1-1 2-2 2H8z" fill="#fff"/></svg></div><div><h4>QUALITY</h4><p>Harbourne delivery quality, effective training facilitated by industry leaders. Just ask our students who rate us on average of 4.7 out of 5.</p></div></div>
    <div class="why-item"><div class="icon"><svg width="24" height="24" viewBox="0 0 24 24"><circle cx="12" cy="12" r="7" fill="none" stroke="#fff" stroke-width="3" stroke-dasharray="3 2"/><circle cx="12" cy="12" r="3" fill="#fff"/></svg></div><div><h4>EXPERIENCE</h4><p>Harbourne is Australia's largest and leading providers of nationally recognised training in health administration – training from over 17 locations Australia wide.</p></div></div>
    <div class="why-item"><div class="icon"><svg width="24" height="24" viewBox="0 0 24 24"><path d="M12 2l3 7h7l-5.5 4.5 2 7.5L12 16.5 5.5 21l2-7.5L2 9h7z" fill="#fff"/></svg></div><div><h4>VALUE</h4><p>Our innovative teaching approach allows us to deliver exceptional training at affordable prices with no hidden extras.</p></div></div>
    <div class="why-item"><div class="icon"><svg width="24" height="24" viewBox="0 0 24 24"><path d="M2 22V12l5-3v3l5-3v3l5-3V3h4v19z" fill="#fff"/></svg></div><div><h4>INDUSTRY RECOGNISED</h4><p>Harbourne work hand in hand with industry to develop our core programme and consolidate the programme annually to keep the programme fresh and relevant.</p></div></div>
    <div class="why-item"><div class="icon"><svg width="24" height="24" viewBox="0 0 24 24"><path d="M3 6h3M9 6h12M3 12h3M9 12h8M3 18h3M9 18h6" stroke="#fff" stroke-width="2.5"/></svg></div><div><h4>GREAT JOB RESULTS</h4><p>Harbourne students get jobs! Our focus is to create job-ready students who are mentored to achieve their goals. Harbourne also provide a recruitment service for industry and graduates.</p></div></div>
  </div>
</section>

<section class="abs blog">
  <h3 class="section-title">Latest Blog</h3>
  <div class="blog-nav">
    <svg width="12" height="16" viewBox="0 0 12 16"><path d="M9 2L3 8l6 6" fill="none" stroke="#222" stroke-width="2.4"/></svg>
    <svg width="12" height="16" viewBox="0 0 12 16"><path d="M3 2l6 6-6 6" fill="none" stroke="#222" stroke-width="2.4"/></svg>
  </div>
  <article class="card" style="left:132px">
    <div class="thumb" role="img" aria-label="Medical staff reviewing notes together" style="background:linear-gradient(135deg,#cfe0ee,#7fa2c4)"></div>
    <div class="date">25<small>JAN</small></div>
    <h5>Short Course Medical Reception Training,</h5>
    <p>The Harbourne Medical Receptionist Training program is geared towards gaining employment and as part...</p>
    <span class="more">READ MORE</span>
  </article>
  <article class="card" style="left:368px">
    <div class="thumb" role="img" aria-label="Brain scan images on a light panel" style="background:linear-gradient(135deg,#2a3a4a,#8a9aa8)"></div>
    <div class="date">14<small>JUNE</small></div>
    <h5>Contrary to popular belief, Lorem Ipsum is not.</h5>
    <p>The Harbourne Medical Receptionist Training program is geared towards gaining employment and as part...</p>
    <span class="more">READ MORE</span>
  </article>
  <article class="card" style="left:606px">
    <div class="thumb" role="img" aria-label="Hospital monitoring equipment" style="background:linear-gradient(135deg,#1e2a36,#5b6f80)"></div>
    <div class="date">13<small>FEB</small></div>
    <h5>The standard chunk of Lorem Ipsum used since.</h5>
    <p>The Harbourne Medical Receptionist Training program is geared towards gaining employment and as part...</p>
    <span class="more">READ MORE</span>
  </article>
  <article class="card" style="left:844px">
    <div class="thumb" role="img" aria-label="Stethoscope lying on a medical chart" style="background:linear-gradient(135deg,#e6eef6,#7ea4cc)"></div>
    <div class="date">25<small>JAN</small></div>
    <h5>Lorem Ipsum is simply dummy text of the printinG.</h5>
    <p>The Harbourne Medical Receptionist Training program is geared towards gaining employment and as part...</p>
    <span class="more">READ MORE</span>
  </article>
</section>

<section class="abs testimonials" role="img" aria-label="Group of smiling professionals behind a blue overlay">
  <h3 class="title">TESTIMONIALS</h3>
  <div class="rule"></div>
  <svg class="abs" style="left:150px;top:110px" width="52" height="40" viewBox="0 0 52 40"><path d="M0 40V20C0 8 6 2 18 0v8c-6 2-8 6-8 12h8v20zM30 40V20C30 8 36 2 48 0v8c-6 2-8 6-8 12h8v20z" fill="rgba(255,255,255,.45)"/></svg>
  <p class="quote">There are many variations of passages of Lorem Ipsum available, but the majority have suffered alteration in some form, by injected humour, or randomised words which don't look even slightly believable. If you are going to use a passage of Lorem Ipsum, you need to be sure there isn't anything embarrassing hidden in the middle of text. All the Lorem Ipsum generators on the Internet tend to repeat predefined chunks as necessary, making this the first true generator.</p>
  <svg class="abs" style="left:468px;top:254px" width="14" height="20" viewBox="0 0 14 20"><path d="M11 2L3 10l8 8" fill="none" stroke="#fff" stroke-width="2.5"/></svg>
  <div class="author"><div class="avatar" role="img" aria-label="Portrait of the reviewer"></div><div><b>DANIEL MARSH</b><span>Australia</span></div></div>
  <svg class="abs" style="left:720px;top:254px" width="14" height="20" viewBox="0 0 14 20"><path d="M3 2l8 8-8 8" fill="none" stroke="#fff" stroke-width="2.5"/></svg>
</section>

<footer class="abs footer">
  <div class="brand">Harbourne Institute of Training<span class="brand-mark"></span></div>
  <div class="vline"></div>
  <div class="contact">
    <div class="foot-h">CONTACT US</div>
    <div class="region">NEW SOUTH WALES, VICTORIA &amp; ACT</div><div class="phone">1800 555 014</div>
    <div class="region">SOUTH AUSTRALIA, QUEENSLAND, NT</div><div class="phone">1800 555 027</div>
    <div class="region">WESTERN AUSTRALIA</div><div class="phone">08 5550 3100</div>
  </div>
  <div class="enquiry">
    <div class="foot-h">ENQUIRY</div>
    <div class="efield" style="left:0;top:32px">Name</div>
    <div class="efield" style="left:0;top:74px">E mail</div>
    <div class="efield" style="left:0;top:116px">Phone</div>
    <div class="efield" style="left:226px;top:32px;width:210px;height:120px">Message</div>
    <a class="btn abs" style="left:346px;top:168px;width:90px;height:34px;font-size:11px">Submit</a>
  </div>
</footer>

<div class="abs bottom">
  <span>Follow us on</span>
  <div class="social"><i></i><i></i><i></i><i></i></div>
  <span style="margin-left:auto">Copyrights @ 2016 All Rights Reserved</span>
</div>

</body>
</html>
```